Brightfen Business Card Redesign & Logo Update

We need to update our business cards to something more modern and fresh. Brightfen can provide the current color schemes and old design examples, but welcome creativity in helping us with this redesign. PLEASE NOTE that we no longer utilize the "tree" and/or "leaf" imagery in our branding. If able would apprecaite an update on the quality of our "words only" logo in Ai. / PNG formats too.

Target Market(s)

Investors, landowners, corporate partners, contractors

Industry/Entity Type

Environmental Restoration & Conservation

Contact Information for Business Card

Logo, persons name, title, mailing address, phone and email, website url

Font styles to use
Other font styles liked:
• Merriweather

Requirements
Nice to have
• Logo, persons name, title, mailing address, phone and email, website url, but open to ideams
Should not have
• No all back backgrounds

```html
<!DOCTYPE html>
<html lang="en">
<head>
<meta charset="utf-8">
<title>Brightfen Business Card</title>
<link rel="stylesheet" href="https://fonts.googleapis.com/css2?family=Merriweather:wght@400;700;900&display=swap">
<style>
  :root {
    --backdrop: #e4e4e4;
    --orange: #cf5c04;
    --orange-light: #de6d14;
    --orange-deep: #c65400;
    --green: #0b6618;
    --paper: #ececec;
    --ink: #1d1d1d;
    --ink-soft: #333333;
    --logo-light: #f1f1f1;
  }
  * { margin: 0; padding: 0; box-sizing: border-box; }
  html, body {
    width: 1200px; height: 831px; overflow: hidden;
    background: var(--backdrop);
    font-family: "Merriweather", Georgia, serif;
  }
  .canvas { position: relative; width: 1200px; height: 831px; }

  .card {
    position: absolute;
    border-radius: 10px;
    overflow: hidden;
  }

  /* Front side */
  .card--front {
    left: 382px; top: 136px; width: 480px; height: 275px;
    background: linear-gradient(200deg, var(--orange-light) 0%, var(--orange) 55%, var(--orange-deep) 100%);
  }
  .card--front .wordmark {
    position: absolute; left: 0; right: 0; top: 116px;
    text-align: center;
    font-weight: 900; font-size: 29px; letter-spacing: 1px;
    color: var(--logo-light);
  }

  /* Back side */
  .card--back {
    left: 384px; top: 440px; width: 482px; height: 277px;
    background: var(--paper);
  }
  .card--back .wordmark {
    position: absolute; right: 26px; top: 30px;
    font-weight: 900; font-size: 24px; letter-spacing: 1px;
    color: var(--green);
  }
  .person-name {
    position: absolute; left: 29px; top: 134px;
    font-weight: 700; font-size: 19px; color: var(--ink);
    letter-spacing: 0.2px;
  }
  .person-title {
    position: absolute; left: 29px; top: 158px;
    font-size: 12px; color: var(--ink-soft);
  }
  .title-rule {
    position: absolute; left: 88px; top: 165px; width: 367px; height: 1px;
    background: var(--orange);
  }
  .contact-list {
    position: absolute; left: 29px; top: 181px; list-style: none;
  }
  .contact-list li {
    display: flex; align-items: center; height: 15.5px;
    font-size: 12px; color: var(--ink-soft);
  }
  .contact-list svg { width: 8px; height: 8px; margin-right: 9px; flex: none; }
  .mailing-address {
    position: absolute; right: 27px; top: 196px;
    text-align: right; font-size: 12px; line-height: 15.5px; color: var(--ink-soft);
    font-style: normal;
  }
  .footer-band { position: absolute; left: 0; bottom: 0; width: 482px; height: 40px; }
</style>
</head>
<body>
<div class="canvas">

  <section class="card card--front">
    <div class="wordmark">BRIGHTFEN</div>
  </section>

  <section class="card card--back">
    <div class="wordmark">BRIGHTFEN</div>

    <h1 class="person-name">OWEN CARVER</h1>
    <p class="person-title">President</p>
    <div class="title-rule"></div>

    <ul class="contact-list">
      <li>
        <svg viewBox="0 0 10 10" aria-hidden="true"><path fill="var(--orange)" d="M2.2 0.6 L3.8 2.6 L2.9 3.6 Q4 6 6.4 7.1 L7.4 6.2 L9.4 7.8 L8.4 9.4 Q2.5 9 0.6 1.6 Z"/></svg>
        555-014-2290
      </li>
      <li>
        <svg viewBox="0 0 10 10" aria-hidden="true"><rect x="0.5" y="2" width="9" height="6.5" fill="var(--orange)"/><path d="M0.8 2.4 L5 5.6 L9.2 2.4" fill="none" stroke="var(--paper)" stroke-width="0.9"/></svg>
        hello@brightfen-mail.com
      </li>
      <li>
        <svg viewBox="0 0 10 10" aria-hidden="true"><circle cx="5" cy="5" r="4.3" fill="none" stroke="var(--orange)" stroke-width="1.1"/><ellipse cx="5" cy="5" rx="1.8" ry="4.3" fill="none" stroke="var(--orange)" stroke-width="0.9"/><path d="M0.8 5 H9.2" stroke="var(--orange)" stroke-width="0.9"/></svg>
        www.brightfen.com
      </li>
    </ul>

    <address class="mailing-address">
      412 fen point<br>
      Marsh road brightfen CA 2345
    </address>

    <svg class="footer-band" viewBox="0 0 482 40" aria-hidden="true">
      <path d="M0 14 Q241 34 482 14" fill="none" stroke="var(--green)" stroke-width="2"/>
      <path fill="var(--orange-deep)" d="M0 22 Q241 42 482 22 L482 40 L0 40 Z"/>
    </svg>
  </section>

</div>
</body>
</html>
```